Car transport business

We need a new business card design. Attached is our old card sample. I would just like to adjust the logo colors (blue and red) to be brighter. I changed my name to the brighter red and the word dispatcher to a brighter blue as an example. But you can adjust those colors further. And then perhaps you can use the same colors for the card design but use your imagination.

As a suggestion so the card stands out I would like to add a clip art of car carrier truck. Attached are examples of that as well

```html
<!DOCTYPE html>
<html lang="en">
<head>
<meta charset="utf-8">
<title>Summit Haul – Business Card</title>
<link href="https://fonts.googleapis.com/css2?family=Roboto:wght@400;500;700;900&display=swap" rel="stylesheet">
<style>
  :root {
    --page-bg: #d9dadc;
    --card-dark: #2a2a2b;
    --art-dark: #151516;
    --brand-red: #ed1c24;
    --brand-blue: #1b6fc4;
    --white: #ffffff;
    --card-radius: 22px;
  }
  * { box-sizing: border-box; margin: 0; padding: 0; }
  html, body {
    width: 1200px; height: 874px; overflow: hidden;
    background: var(--page-bg);
    font-family: "Roboto", Arial, sans-serif;
  }
  .stage {
    width: 1200px; height: 874px;
    display: flex; flex-direction: column; align-items: center; justify-content: center;
    gap: 40px;
  }
  .card {
    position: relative;
    width: 640px; height: 366px;
    border-radius: var(--card-radius);
    overflow: hidden;
    box-shadow: 0 10px 26px rgba(0,0,0,0.25);
  }

  /* Back side */
  .card-back { background: linear-gradient(135deg, #323233 0%, var(--card-dark) 55%, #222223 100%); }
  .truck-art {
    position: absolute; left: 20px; top: 90px; width: 620px; height: 276px;
    background:
      radial-gradient(ellipse 55% 48% at 42% 58%, var(--art-dark) 0%, rgba(21,21,22,0.75) 45%, rgba(21,21,22,0) 100%),
      radial-gradient(ellipse 40% 35% at 78% 70%, rgba(21,21,22,0.7) 0%, rgba(21,21,22,0) 100%);
  }
  .back-brand {
    position: absolute; right: 40px; top: 60px; width: 400px;
    text-align: right;
  }
  .brand-name {
    font-weight: 900; letter-spacing: 0.06em; text-transform: uppercase;
    color: var(--brand-blue); line-height: 1;
    white-space: nowrap;
  }
  .back-brand .brand-name { font-size: 44px; }
  .brand-tagline {
    font-weight: 400; text-transform: uppercase; letter-spacing: 0.22em;
    color: var(--brand-blue); line-height: 1;
    white-space: nowrap;
  }
  .back-brand .brand-tagline { font-size: 11px; margin-top: 9px; }

  /* Front side */
  .card-front { background: var(--brand-red); }
  .front-shape { position: absolute; inset: 0; }
  .contact {
    position: absolute; left: 36px; top: 34px;
    color: var(--white);
  }
  .contact-name { font-size: 26px; font-weight: 900; letter-spacing: 0.02em; text-transform: uppercase; }
  .contact-role { font-size: 15px; font-weight: 500; margin-top: 2px; }
  .contact-list { list-style: none; margin-top: 16px; font-size: 15px; line-height: 1.3; }
  .front-brand {
    position: absolute; left: 270px; top: 222px; width: 340px;
    text-align: center;
  }
  .front-brand .brand-name { font-size: 36px; }
  .front-brand .brand-tagline { font-size: 9.5px; margin-top: 8px; }
</style>
</head>
<body>
<main class="stage">

  <section class="card card-back" aria-label="Card back">
    <div class="truck-art" role="img" aria-label="Car carrier truck illustration in dark tones"></div>
    <div class="back-brand">
      <div class="brand-name">Summit Haul</div>
      <div class="brand-tagline">The Auto Transport Professionals</div>
    </div>
  </section>

  <section class="card card-front" aria-label="Card front">
    <svg class="front-shape" width="640" height="366" viewBox="0 0 640 366" aria-hidden="true">
      <circle cx="500" cy="470" r="330" fill="none" stroke="var(--brand-blue)" stroke-width="12"/>
      <circle cx="500" cy="470" r="322" fill="var(--white)"/>
    </svg>

    <div class="contact">
      <div class="contact-name">Dale Morven</div>
      <div class="contact-role">Dispatcher</div>
      <ul class="contact-list">
        <li>(P) 555-201-0148</li>
        <li>(M) 555-201-0172</li>
        <li>summithaulinc@mail.com</li>
        <li>www.summithaulinc.com</li>
      </ul>
    </div>

    <div class="front-brand">
      <div class="brand-name">Summit Haul</div>
      <div class="brand-tagline">The Auto Transport Professionals</div>
    </div>
  </section>

</main>
</body>
</html>
```